Veltrano.co - Polar Expeditions Specialists

We need a modern, visually striking business card for Veltrano.co, a company specialized in selling expedition cruises to the most remote regions on Earth, with a focus on the Arctic and Antarctica. The design should instantly communicate that the cardholder is an expert in polar travel. Use clean, premium aesthetics with cool tones like icy blue and white, possibly incorporating polar imagery (ice, glaciers, penguins, etc.)

Attached the logo

Contact Information for Business Card

Feels high-end and trustworthy.. Visually memorable — encourages people to keep it

Colors
0054AA
0677BA
7BADD7
CADEEF
E8F1F8

Requirements
Must have
• ice, glaciers, penguins, montains
Nice to have
• modern, transparente,

```html
<!DOCTYPE html>
<html lang="en">
<head>
<meta charset="utf-8">
<title>Veltrano.co Business Card</title>
<link href="https://fonts.googleapis.com/css2?family=Poppins:wght@500;600;700&family=Montserrat:wght@400;500;700&display=swap" rel="stylesheet">
<style>
  :root {
    --brand-blue: #2a74b9;
    --deep-blue: #0054aa;
    --mid-blue: #0677ba;
    --soft-blue: #7badd7;
    --pale-blue: #cadeef;
    --ice: #e8f1f8;
    --paper: #ffffff;
    --ink: #1f1f24;
    --backdrop: #c9c9c9;
  }
  * { box-sizing: border-box; margin: 0; padding: 0; }
  html, body { width: 1200px; height: 788px; overflow: hidden; }
  body {
    background: var(--backdrop);
    display: flex;
    align-items: center;
    justify-content: center;
    gap: 40px;
    font-family: "Montserrat", sans-serif;
  }
  .card {
    width: 540px;
    height: 309px;
    border-radius: 22px;
    overflow: hidden;
    position: relative;
    box-shadow: 0 10px 24px rgba(0,0,0,0.18);
  }

  /* Contact side */
  .card-contact { background: var(--paper); display: flex; }
  .brand-band {
    width: 150px;
    background: var(--brand-blue);
    position: relative;
    display: flex;
    align-items: center;
    justify-content: center;
  }
  .band-lockup {
    transform: rotate(90deg);
    display: flex;
    flex-direction: column;
    align-items: center;
    color: var(--paper);
    font-family: "Poppins", sans-serif;
    white-space: nowrap;
  }
  .band-lockup .lockup-row { display: flex; align-items: center; gap: 8px; }
  .band-lockup .dot { width: 20px; height: 20px; border-radius: 50%; background: var(--paper); }
  .band-lockup .name { font-size: 30px; font-weight: 700; line-height: 1; }
  .band-lockup .tagline { font-size: 9px; font-weight: 500; margin-top: 4px; }

  .contact-body { padding: 52px 0 0 40px; color: var(--ink); }
  .person-name {
    font-family: "Montserrat", sans-serif;
    font-weight: 700;
    font-size: 24px;
    letter-spacing: 0.5px;
    color: var(--mid-blue);
    line-height: 1;
  }
  .person-role { font-size: 15px; margin-top: 4px; }
  .address { font-size: 14px; line-height: 1.35; margin-top: 18px; }
  .contact-list { list-style: none; margin-top: 16px; font-size: 14px; line-height: 1.55; }
  .contact-list li { display: flex; align-items: center; gap: 8px; }
  .contact-list svg { width: 11px; height: 11px; fill: var(--mid-blue); flex: none; }

  /* Brand side */
  .card-brand {
    background: var(--brand-blue);
    display: flex;
    align-items: center;
    padding-left: 48px;
  }
  .polar-art {
    position: absolute;
    right: -20px;
    top: -30px;
    width: 300px;
    height: 380px;
    border-radius: 50%;
    background: radial-gradient(circle at 50% 45%, rgba(123,173,215,0.35), rgba(123,173,215,0) 70%);
  }
  .brand-lockup { position: relative; display: flex; align-items: center; gap: 16px; color: var(--paper); font-family: "Poppins", sans-serif; }
  .brand-lockup .dot { width: 60px; height: 60px; border-radius: 50%; background: var(--paper); flex: none; }
  .brand-lockup .name { font-size: 56px; font-weight: 700; line-height: 1; letter-spacing: 0.5px; }
  .brand-lockup .tagline { font-size: 16px; font-weight: 600; margin-top: 4px; }
</style>
</head>
<body>
  <section class="card card-contact">
    <div class="brand-band">
      <div class="band-lockup">
        <div class="lockup-row"><span class="dot"></span><span class="name">Veltrano.co</span></div>
        <span class="tagline">Polar Expeditions Specialists</span>
      </div>
    </div>
    <div class="contact-body">
      <h1 class="person-name">MARTIN HALE</h1>
      <p class="person-role">CEO / Founder</p>
      <p class="address">P.O. Box 3196 Harbor Lane<br>Northport AV 7810</p>
      <ul class="contact-list">
        <li><svg viewBox="0 0 24 24"><path d="M6.6 10.8a15 15 0 0 0 6.6 6.6l2.2-2.2a1 1 0 0 1 1-.25 11 11 0 0 0 3.6.6 1 1 0 0 1 1 1V20a1 1 0 0 1-1 1A17 17 0 0 1 3 4a1 1 0 0 1 1-1h3.5a1 1 0 0 1 1 1 11 11 0 0 0 .6 3.6 1 1 0 0 1-.25 1z"/></svg>+43 612 48 30 517</li>
        <li><svg viewBox="0 0 24 24"><path d="M2 5h20v14H2z M2 5l10 8 10-8" /></svg>martin.hale@veltrano.co</li>
        <li><svg viewBox="0 0 24 24"><circle cx="12" cy="12" r="10"/></svg>www.veltrano.co</li>
      </ul>
    </div>
  </section>

  <section class="card card-brand">
    <div class="polar-art" role="img" aria-label="Faint polar bear and penguin silhouettes against icy blue"></div>
    <div class="brand-lockup">
      <span class="dot"></span>
      <div>
        <div class="name">Veltrano.co</div>
        <div class="tagline">Polar Expeditions Specialists</div>
      </div>
    </div>
  </section>
</body>
</html>
```